Updated website design needed for Radiology Group, Pine Hollow Imaging Partners

Clean, uncluttered, updated design needed for top regional Radiology Center. Focus on personal, patient oriented design, (not clinical). Should be simple and easy to navigate, with clear CTAs. Use blues, greens and photos of people in the Central Oregon outdoors.
Uncoded, PSD design only. 2 pages: Home page and one example interior page.
reference current site: http://www.phipclinic-example.com/
Sites they like:
http://www.valescanlabs-example.com/
http://www.tbmx-example.net/handler.cfm?event=practice,main
http://www.kestrelbonecare-example.com/

Medical Imaging

2 page

Sans Serif

• Personal and patient friendly.
• Lots of white space, clean and uncluttered. Clear CTAs, such as: Patient Bill Pay, Make an Appointment, Meet Our Doctors
• Use copy and contact information from the current site.
• Use outdoor images from Central Oregon, late Winter/ Spring (snow, light colors, spring green, for example)
• Include one example interior page, either Your Exam or Meet Our Doctors
• The client likes:
• Meet Our Doctors slider section, and big, easy to navigate Information Center on www.kestrelbonecare-example.com
• The personal feel of the Your Exam section on www.valescanlabs-example.com
• Blues and Greens, outdoorsy imagery
• The client does not like:
• complex drop down menus
• clinical feel
• Do not use lorum ipsum or dummy text.
• Do not use outdoor images from other regions. Do not use Summer (hot, poolside) or Fall (red/orange leaves) images.

```html
<!DOCTYPE html>
<html lang="en">
<head>
<meta charset="utf-8">
<title>Pine Hollow Imaging Partners</title>
<link rel="stylesheet" href="https://fonts.googleapis.com/css2?family=Open+Sans:wght@400;600&family=Raleway:wght@400;500;600&display=swap">
<style>
:root{
  --accent:#4f6fa3;
  --accent-dark:#41608f;
  --green:#5f9a5a;
  --green-light:#8cc27f;
  --ink:#1d1d1f;
  --muted:#8a8a92;
  --body:#666;
  --black:#000;
  --panel:#e3e3e3;
  --footer-bg:#f1f2f4;
  --white:#fff;
}
*{box-sizing:border-box;margin:0;padding:0}
html,body{width:1200px;height:2532px;overflow:hidden;background:var(--white)}
body{position:relative;font-family:"Open Sans",Arial,sans-serif;color:var(--body)}

/* header */
.site-header{position:absolute;left:0;top:0;width:1200px;height:108px;background:var(--white)}
.brand{position:absolute;left:47px;top:16px;display:flex;align-items:center;gap:12px}
.brand-mark{width:70px;height:70px;background:var(--accent)}
.brand-name{font-family:"Open Sans",Arial,sans-serif;font-size:21px;line-height:1.15;color:var(--ink);width:160px}
.contact{position:absolute;top:30px;width:180px;text-align:center;font-size:18px;line-height:28px}
.contact-label{color:var(--accent);font-weight:600}
.contact-phone{color:var(--muted)}
.contact-divider{position:absolute;top:28px;width:1px;height:52px;background:#d9d9de}

/* nav */
.main-nav{position:absolute;left:0;top:108px;width:1200px;height:63px;background:var(--black);display:flex;align-items:center;padding-left:47px;font-size:14px;color:var(--white)}
.main-nav a{color:var(--white);text-decoration:none;padding:0 20px;line-height:63px}
.main-nav a.active{background:var(--green);padding:0 22px}
.main-nav .sep{color:var(--white)}

/* hero */
.hero{position:absolute;left:0;top:171px;width:1200px;height:600px;overflow:hidden}
.hero-photo{position:absolute;inset:0;background:linear-gradient(180deg,#cfe0ef 0%,#eef3f6 38%,#f7f8f6 55%,#c9dcb5 80%,#8fb47c 100%)}
.hero-panel{position:absolute;left:0;top:0}
.hero-title{position:absolute;right:45px;top:148px;width:560px;text-align:right;font-family:"Raleway",Arial,sans-serif;font-weight:500;font-size:37px;line-height:42px;color:var(--white)}
.hero-text{position:absolute;right:45px;top:262px;width:420px;text-align:right;font-size:12.5px;line-height:22px;color:var(--white)}
.hero-btn{position:absolute;left:1031px;top:364px;width:127px;height:42px;background:var(--white);color:var(--ink);font-size:12px;line-height:42px;text-align:center}
.dots{position:absolute;display:flex;gap:9px}
.dot{width:14px;height:14px;border-radius:50%;border:1.5px solid var(--white)}
.dot.on{background:var(--white)}

/* quick links */
.quick-links{position:absolute;left:51px;top:631px;width:1107px;height:199px;background:var(--panel);box-shadow:0 18px 22px -14px rgba(0,0,0,.35)}
.tile{position:absolute;top:37px;width:132px;height:130px;background:var(--white);text-align:center;color:var(--accent);font-family:"Raleway",Arial,sans-serif;font-weight:500;font-size:16.5px;line-height:20px}
.tile svg{display:block;margin:22px auto 10px;width:44px;height:44px}

/* welcome */
.welcome-title{position:absolute;left:0;top:862px;width:1200px;text-align:center;font-family:"Raleway",Arial,sans-serif;font-weight:500;font-size:29px;color:var(--ink)}
.welcome-title span{color:var(--accent)}
.welcome-text{position:absolute;left:127px;top:922px;width:946px;text-align:center;font-size:11.5px;line-height:21px;color:var(--body)}
.btn-small{position:absolute;background:var(--green);color:var(--white);font-size:11px;text-align:center;border:1px solid #4b7f47}

/* services */
.services{position:absolute;left:0;top:1097px;width:1200px;height:643px;overflow:hidden}
.services-bg{position:absolute;inset:0;background:radial-gradient(ellipse at 50% 40%,#28332b 0%,#161a17 55%,#0b0d0b 100%)}
.section-title{position:absolute;left:0;width:1200px;text-align:center;font-family:"Raleway",Arial,sans-serif;font-weight:500;font-size:29px;color:var(--white)}
.section-title span{color:var(--green-light)}
.service{position:absolute;width:410px}
.service h3{font-family:"Open Sans",Arial,sans-serif;font-weight:400;font-size:21px;color:var(--white);margin-bottom:8px}
.service p{font-size:11.5px;line-height:20px;color:#ddd}
.service .more{display:block;font-size:11px;color:var(--green-light);margin-top:7px}
.service.left{left:24px;text-align:right}
.service.right{left:765px;text-align:left}
.thumb{position:absolute;width:92px;height:92px;border:3px solid var(--white)}

/* testimonials */
.testimonials{position:absolute;left:0;top:1740px;width:1200px;height:414px;background:var(--accent)}
.quote-icon{position:absolute;left:561px;top:32px;width:78px;height:78px;border:2px solid var(--white);border-radius:50%}
.t-line{position:absolute;background:rgba(255,255,255,.75)}
.t-quote{position:absolute;left:110px;top:240px;width:980px;text-align:center;font-size:12.5px;line-height:29px;color:var(--white);font-weight:600}
.t-name{position:absolute;left:0;top:306px;width:1200px;text-align:center;font-size:15px;line-height:20px;color:var(--white)}

/* footer */
.site-footer{position:absolute;left:0;top:2154px;width:1200px;height:283px;background:var(--footer-bg)}
.footer-brand{position:absolute;left:93px;top:77px;display:flex;align-items:center;gap:12px}
.footer-col{position:absolute;top:27px;height:209px;border-left:1px solid #d5d6db;padding-left:30px}
.footer-col h4{font-family:"Raleway",Arial,sans-serif;font-weight:600;font-size:16px;color:var(--accent-dark);margin-top:16px;margin-bottom:12px}
.footer-col li{list-style:none;font-size:11.5px;color:var(--muted);line-height:28.5px;padding-left:14px;position:relative}
.footer-col li::before{content:"";position:absolute;left:0;top:13px;width:4px;height:4px;border-radius:50%;background:#b3b3bb}

/* bottom bar */
.bottom-bar{position:absolute;left:0;top:2437px;width:1200px;height:95px;background:var(--black)}
.copyright{position:absolute;left:47px;top:40px;font-size:11.5px;color:#cfcfcf}
.social{position:absolute;top:33px;width:29px;height:29px;border:1.5px solid var(--white)}
</style>
</head>
<body>

<header class="site-header">
  <div class="brand">
    <div class="brand-mark"></div>
    <div class="brand-name">Pine Hollow Imaging Partners</div>
  </div>
  <div class="contact" style="left:425px"><div class="contact-label">Medical Records:</div><div class="contact-phone">(555) 210-4471</div></div>
  <div class="contact-divider" style="left:615px"></div>
  <div class="contact" style="left:617px"><div class="contact-label">Billing:</div><div class="contact-phone">(555) 210-4482</div></div>
  <div class="contact-divider" style="left:800px"></div>
  <div class="contact" style="left:803px"><div class="contact-label">Scheduling:</div><div class="contact-phone">(555) 210-4493</div></div>
  <div class="contact-divider" style="left:985px"></div>
  <div class="contact" style="left:980px"><div class="contact-label">Main Line:</div><div class="contact-phone">(555) 210-4400</div></div>
</header>

<nav class="main-nav">
  <a class="active">Home</a><a>About Us</a><span class="sep">|</span><a>Our Service</a><span class="sep">|</span><a>For Patients</a><span class="sep">|</span><a>Our Physicians</a><span class="sep">|</span><a>For Physicians</a><span class="sep">|</span><a>PACS &amp; Document</a><span class="sep">|</span><a>Appointment</a><span class="sep">|</span><a>Our Location</a>
</nav>

<section class="hero">
  <div class="hero-photo" role="img" aria-label="Photo of a patient and caregiver walking a snowy pine trail in early spring, fresh green meadow below"></div>
  <svg class="hero-panel" width="1200" height="600" viewBox="0 0 1200 600" aria-hidden="true">
    <path d="M795 0H1200V600H600V470C615 300 700 140 795 0Z" fill="#4f6fa3"/>
  </svg>
  <h1 class="hero-title">Welcome to Pine Hollow Imaging Partners</h1>
  <p class="hero-text">Caring, expert medical imaging close to home. Our board-certified radiologists and friendly technologists guide you through every exam with clear answers, short waits and results sent quickly to your doctor.</p>
  <div class="hero-btn">Read More</div>
  <div class="dots" style="left:792px;top:398px"><span class="dot"></span><span class="dot"></span><span class="dot"></span><span class="dot on"></span><span class="dot"></span></div>
</section>

<section class="quick-links">
  <div class="tile" style="left:40px">
    <svg viewBox="0 0 44 44" fill="none" stroke="#4f6fa3" stroke-width="2.5"><path d="M9 3h18l9 9v29H9z"/><path d="M27 3v9h9M15 20h15M15 26h15M15 32h15"/></svg>Patient Bill<br>Pay</div>
  <div class="tile" style="left:189px">
    <svg viewBox="0 0 44 44" fill="none" stroke="#4f6fa3" stroke-width="3"><circle cx="22" cy="22" r="18"/><path d="M22 11v11h8"/></svg>Make an<br>Appointment</div>
  <div class="tile" style="left:337px">
    <svg viewBox="0 0 44 44" fill="#4f6fa3"><circle cx="22" cy="12" r="9"/><path d="M5 42c0-11 7-17 17-17s17 6 17 17z"/><rect x="19" y="29" width="6" height="8" fill="#fff"/></svg>Meet Our<br>Doctors</div>
  <div class="tile" style="left:489px">
    <svg viewBox="0 0 44 44" fill="#4f6fa3"><path d="M22 2c-8 0-14 6-14 14 0 10 14 26 14 26s14-16 14-26c0-8-6-14-14-14z"/><circle cx="22" cy="16" r="5" fill="#fff"/></svg>Find a<br>Location</div>
  <div class="tile" style="left:636px">
    <svg viewBox="0 0 44 44" fill="none" stroke="#4f6fa3" stroke-width="2.5"><rect x="8" y="6" width="28" height="35"/><path d="M19 6V2h6v4M14 14h4M26 14h4M14 21h4M26 21h4M14 28h4M26 28h4M19 41v-7h6v7"/></svg>Events &amp;<br>Classes</div>
  <div class="tile" style="left:784px">
    <svg viewBox="0 0 44 44" fill="#4f6fa3"><rect x="6" y="3" width="22" height="30"/><rect x="15" y="11" width="23" height="31" stroke="#fff" stroke-width="2"/></svg><br>Career</div>
  <div class="tile" style="left:933px">
    <svg viewBox="0 0 44 44" fill="#4f6fa3"><ellipse cx="17" cy="16" rx="15" ry="11"/><path d="M8 24l-3 8 9-5z"/><ellipse cx="29" cy="27" rx="13" ry="9" stroke="#fff" stroke-width="2"/><path d="M36 33l4 7-9-4z"/></svg>Patient<br>Testimonials</div>
</section>

<h2 class="welcome-title">Welcome to <span>Pine Hollow Imaging Partners</span></h2>
<p class="welcome-text">For over thirty years our local team of radiologists has served families across the high desert and the mountain towns around it. We offer the full range of modern imaging, from digital mammography to MRI, in calm and welcoming clinics. Our staff take the time to explain each step, answer your questions and help you feel at ease. Book online, call our scheduling line, or visit any of our convenient locations today.</p>
<div class="btn-small" style="left:550px;top:1012px;width:122px;height:36px;line-height:34px">READ MORE</div>

<section class="services">
  <div class="services-bg" role="img" aria-label="Dimmed photo of a snowy pine forest at dusk"></div>
  <h2 class="section-title" style="top:62px">Our <span>Service</span></h2>

  <div class="service left" style="top:137px"><h3>Virtual Colonoscopy (VC)</h3><p>A gentle CT scan of the colon that needs no sedation,<br>so most patients return to normal activity the same day.</p><span class="more">READ MORE ▸</span></div>
  <div class="thumb" role="img" aria-label="Illustration of the colon" style="left:452px;top:143px;background:linear-gradient(135deg,#2f5fa8,#c85a4a)"></div>
  <div class="thumb" role="img" aria-label="Photo of a patient entering an MRI scanner" style="left:648px;top:143px;background:linear-gradient(135deg,#a9b4bd,#e4e8ea)"></div>
  <div class="service right" style="top:137px"><h3>Magnetic Resonance Imaging (MRI)</h3><p>Detailed pictures of joints, spine and organs using<br>magnets, with open-bore scanners for added comfort.</p><span class="more">READ MORE ▸</span></div>

  <div class="service left" style="top:287px"><h3>Digital Mammography</h3><p>Low-dose screening with 3D tomosynthesis and a caring,<br>all-female team that helps you feel at ease.</p><span class="more">READ MORE ▸</span></div>
  <div class="thumb" role="img" aria-label="Mammogram scan image" style="left:452px;top:293px;background:radial-gradient(circle at 55% 50%,#9a9a9a,#1a1a1a 75%)"></div>
  <div class="thumb" role="img" aria-label="Photo of a patient in a CT scanner" style="left:648px;top:293px;background:linear-gradient(135deg,#c5d3de,#eef1f3)"></div>
  <div class="service right" style="top:287px"><h3>Computed Tomography (CT)</h3><p>Fast, precise cross-section scans of the body, with<br>low-dose settings tuned for every patient.</p><span class="more">READ MORE ▸</span></div>

  <div class="service left" style="top:444px"><h3>Ultrasound</h3><p>Safe, radiation-free imaging using sound waves, ideal<br>for pregnancy, abdomen, vessels and soft tissue.</p><span class="more">READ MORE ▸</span></div>
  <div class="thumb" role="img" aria-label="Photo of an ultrasound probe in use" style="left:452px;top:450px;background:linear-gradient(135deg,#e9e4e2,#b9c2cc)"></div>
  <div class="thumb" role="img" aria-label="Photo of a general radiography room" style="left:648px;top:450px;background:linear-gradient(135deg,#8fa6b8,#dfe4e8)"></div>
  <div class="service right" style="top:444px"><h3>General Radiography</h3><p>Quick walk-in X-rays for bones, chest and joints, with<br>images read by our radiologists the same day.</p><span class="more">READ MORE ▸</span></div>
</section>

<section class="testimonials">
  <div class="quote-icon">
    <svg width="74" height="74" viewBox="0 0 74 74" aria-hidden="true"><path d="M37 20c-11 0-19 7-19 15 0 5 3 9 7 12l-3 8 10-5c2 0 3 1 5 1 11 0 19-7 19-16s-8-15-19-15z" fill="#fff"/><rect x="30" y="30" width="4" height="8" fill="#4f6fa3"/><rect x="39" y="30" width="4" height="8" fill="#4f6fa3"/></svg>
  </div>
  <h2 class="section-title" style="top:124px;font-size:28px;color:var(--white)">Client Testimonials</h2>
  <div class="t-line" style="left:600px;top:168px;width:2px;height:58px"></div>
  <p class="t-quote">The staff made my MRI feel easy from start to finish. Everyone was warm and patient, explained each step, and my doctor had the results the very next morning. I would not go anywhere else.</p>
  <div class="t-line" style="left:443px;top:316px;width:95px;height:1px"></div>
  <div class="t-name">Marcus Hale</div>
  <div class="t-line" style="left:662px;top:316px;width:95px;height:1px"></div>
  <div class="dots" style="left:577px;top:350px"><span class="dot" style="width:11px;height:11px"></span><span class="dot on" style="width:11px;height:11px"></span><span class="dot" style="width:11px;height:11px"></span></div>
</section>

<footer class="site-footer">
  <div class="footer-brand">
    <div class="brand-mark" style="width:76px;height:76px"></div>
    <div class="brand-name">Pine Hollow Imaging Partners</div>
  </div>
  <div class="footer-col" style="left:375px">
    <h4>Important Links</h4>
    <ul><li>Affiliate Program</li><li>Special Promotions</li><li>Newsletter</li><li>Contact</li></ul>
  </div>
  <div class="footer-col" style="left:655px">
    <h4>Categories</h4>
    <ul><li>For Patients</li><li>Our Physician</li><li>PACS &amp; Documen</li><li>Appointment</li></ul>
  </div>
  <div class="footer-col" style="left:937px">
    <h4>Navigation</h4>
    <ul><li>About Us</li><li>Services</li><li>Team</li><li>Testimonials</li><li>Contact Us</li></ul>
  </div>
</footer>

<div class="bottom-bar">
  <p class="copyright">Copyright 2016 Company Name.&nbsp; All Rights Reserved.</p>
  <span class="social" style="left:1040px" aria-label="Social profile 1"></span>
  <span class="social" style="left:1081px" aria-label="Social profile 2"></span>
  <span class="social" style="left:1122px" aria-label="Social profile 3"></span>
</div>

</body>
</html>
```